Psychiatric Office Needs a Website- 1st Time Ever!

Been in practice since 2003 with no website, but finally ready to dive in. We are Maplecrest Behavioral Healthcare, a mental health outpatient practice based in Fayetteville, Georgia that sees diverse individuals and families from childhood to advanced age for a variety of conditions. We've grown by word of mouth and referral but would now like to have a digital footprint. Be the pioneer of our website and we will be sure to share. We would like to see designs that are modern, animated, fairly colorful, easy to read, and caters to all ages. Also, we would like the design to take the whole page (not be centered) and can be viewed well on phone/tablet. Please see our outline for more information. Our motto/slogan is: Maplecrest Behavioral Healthcare- A step forward in your wellness journey, so the design should try to reflect that.
Updates

Project Deadline Extended
Reason: site in progress

Target Market(s)

Children through elderly

Industry/Entity Type

Medical

Logo Text

Stepping forward in your wellness journey

Number of Pages Required

1 page

Colors

Designer to choose colors to be used in the design.

Requirements
Must have
• Animation or moving pictures.
• Color.
• Concise.
• User friendly
• Diversity in the stock photos

```html
<!DOCTYPE html>
<html lang="en">
<head>
<meta charset="utf-8">
<title>Maplecrest Behavioral Healthcare</title>
<link href="https://fonts.googleapis.com/css2?family=Open+Sans:wght@300;400;600;700&display=swap" rel="stylesheet">
<style>
:root{
  --blue:#29b5e8;
  --blue-dark:#1e9fd0;
  --orange:#f7941d;
  --ink:#333333;
  --text:#6b6b6b;
  --muted:#9a9a9a;
  --line:#d9d9d9;
  --bg-soft:#f3f3f3;
  --white:#ffffff;
}
*{box-sizing:border-box;margin:0;padding:0}
html,body{width:1200px;height:3523px;overflow:hidden}
body{font-family:"Open Sans",Arial,sans-serif;color:var(--text);background:var(--white);position:relative}
.abs{position:absolute}
svg{display:block}

/* header */
.site-header{position:absolute;left:0;top:0;width:1200px;height:160px;background:var(--white)}
.brand{left:99px;top:50px;display:flex;align-items:center;gap:12px}
.brand-dot{width:48px;height:48px;border-radius:50%;background:var(--blue)}
.brand-name{font-size:19px;font-weight:600;color:var(--blue);line-height:1.2;width:220px}
.info-item{top:70px;display:flex;align-items:center;gap:12px;font-size:12px;color:var(--ink);line-height:1.5}
.info-icon{width:44px;height:44px;border-radius:50%;background:var(--blue);display:flex;align-items:center;justify-content:center}
.info-item strong{font-weight:700}
.portal-btn{left:939px;top:73px;width:160px;height:42px;background:var(--orange);color:var(--white);font-size:14px;font-weight:600;display:flex;align-items:center;justify-content:center;letter-spacing:.3px}

/* nav */
.main-nav{position:absolute;left:0;top:160px;width:1200px;height:47px;background:var(--blue)}
.main-nav a{position:absolute;top:0;height:47px;line-height:47px;color:var(--white);font-size:14px;text-decoration:none;text-transform:uppercase;padding:0 14px}
.main-nav a.active{background:var(--orange)}
.nav-search{position:absolute;left:1086px;top:15px}

/* hero */
.hero{position:absolute;left:0;top:207px;width:1200px;height:545px;overflow:hidden}
.hero-photo{position:absolute;inset:0;background:linear-gradient(100deg,#9a9a9a 0%,#c9c9c9 35%,#e6e6e6 60%,#b5b5b5 100%)}
.hero-title{position:absolute;left:0;width:1200px;top:120px;text-align:center;color:var(--white);font-size:52px;font-weight:700;text-shadow:0 2px 6px rgba(0,0,0,.25)}
.hero-sub{position:absolute;left:0;width:1200px;top:185px;text-align:center;color:var(--white);font-size:32px;font-weight:300;text-shadow:0 2px 6px rgba(0,0,0,.25)}
.hero-btn{position:absolute;left:477px;top:251px;width:246px;height:52px;background:var(--blue);color:var(--white);font-size:20px;font-weight:600;display:flex;align-items:center;justify-content:center;letter-spacing:.5px}
.hero-arrow{position:absolute;top:200px}
.hero-curve{position:absolute;left:0;bottom:0}

/* welcome */
.welcome{position:absolute;left:0;top:752px;width:1200px;height:394px;text-align:center}
.section-title{font-weight:300;color:var(--ink);font-size:33px;letter-spacing:.5px;text-align:center}
.welcome .section-title{color:var(--blue);font-size:32px;margin-top:24px}
.welcome p{width:1060px;margin:18px auto 0;font-size:12.5px;line-height:22px;color:var(--text)}
.outline-btn{position:absolute;border:2px solid var(--blue);color:var(--blue);font-size:16px;font-weight:600;display:flex;align-items:center;justify-content:center;letter-spacing:.4px;background:transparent}

/* services */
.services{position:absolute;left:0;top:1146px;width:1200px;height:650px;background:var(--bg-soft)}
.services .section-title{position:absolute;top:56px;width:1200px}
.service-card{position:absolute;top:141px;width:234px;height:352px;background:var(--white)}
.service-photo{height:181px}
.service-card h3{font-size:17px;font-weight:400;color:var(--ink);line-height:21px;margin:18px 18px 0 18px;height:42px}
.service-card p{font-size:12px;line-height:18px;color:var(--muted);margin:10px 18px 0 18px}

/* faq */
.faq{position:absolute;left:0;top:1796px;width:1200px;height:477px;overflow:hidden}
.faq-photo{position:absolute;inset:0;background:linear-gradient(160deg,#3cbbe9 0%,#29ace0 50%,#1c9bd2 100%)}
.faq .section-title{position:absolute;top:64px;width:1200px;color:var(--white)}
.faq-list{position:absolute;left:164px;top:168px;width:700px}
.faq-q{font-size:17px;font-weight:700;color:var(--white);line-height:24px}
.faq-a{font-size:13.5px;color:#dff4fc;margin-top:12px;margin-bottom:28px}

/* news */
.news{position:absolute;left:0;top:2273px;width:1200px;height:584px}
.news .section-title{position:absolute;top:64px;width:1200px}
.news-intro{position:absolute;left:190px;top:140px;width:820px;text-align:center;font-size:12.5px;line-height:26px;color:var(--text)}
.news-item{position:absolute;top:235px;width:308px}
.news-photo{height:157px}
.news-item h3{font-size:18px;font-weight:600;color:var(--ink);margin-top:20px}
.news-item p{font-size:12px;line-height:18px;color:var(--text);margin-top:12px}
.news-date{font-size:14px;color:var(--ink);margin-top:12px;padding-left:4px}

/* contact */
.contact{position:absolute;left:0;top:2857px;width:1200px;height:590px;background:var(--bg-soft)}
.contact .section-title{position:absolute;top:56px;width:1200px}
.contact-info{position:absolute;left:101px;top:168px;width:420px;font-size:17px;color:var(--ink);line-height:28px}
.contact-row{display:flex;gap:12px;margin-bottom:12px}
.contact-row svg{flex:none;margin-top:6px}
.contact-row b{font-weight:700}
.social-dot{width:36px;height:36px;border-radius:50%;background:var(--blue);margin-top:20px}
.contact-form{position:absolute;left:547px;top:164px;width:552px}
.field{position:absolute;height:40px;border:1px solid var(--line);background:var(--white);font-size:11px;color:#aaa;padding:12px 14px}
.submit-btn{position:absolute;left:0;top:315px;width:124px;height:38px;background:var(--orange);color:var(--white);font-size:13px;font-weight:600;display:flex;align-items:center;justify-content:center}

/* footer */
.site-footer{position:absolute;left:0;top:3447px;width:1200px;height:76px;background:var(--blue);color:var(--white);font-size:13px;text-align:center;line-height:76px}
</style>
</head>
<body>

<header class="site-header">
  <div class="abs brand">
    <span class="brand-dot"></span>
    <span class="brand-name">Maplecrest Behavioral Healthcare</span>
  </div>
  <div class="abs info-item" style="left:432px">
    <span class="info-icon">
      <svg width="22" height="22" viewBox="0 0 22 22"><circle cx="11" cy="11" r="8.5" fill="none" stroke="#fff" stroke-width="2"/><path d="M11 6v5.5l3.5 2" fill="none" stroke="#fff" stroke-width="2" stroke-linecap="round"/></svg>
    </span>
    <span><strong>Monday-Friday: 9am to 5pm</strong><br>Saturday / Sunday: Closed</span>
  </div>
  <div class="abs info-item" style="left:706px">
    <span class="info-icon">
      <svg width="20" height="20" viewBox="0 0 24 24"><path d="M6.6 10.8a15.1 15.1 0 0 0 6.6 6.6l2.2-2.2a1 1 0 0 1 1-.25c1.1.37 2.3.57 3.6.57a1 1 0 0 1 1 1V20a1 1 0 0 1-1 1C10.6 21 3 13.4 3 4a1 1 0 0 1 1-1h3.5a1 1 0 0 1 1 1c0 1.3.2 2.5.57 3.6a1 1 0 0 1-.25 1z" fill="#fff"/></svg>
    </span>
    <span><strong>(770) 555-0142</strong><br>hello@maplecrestbh.com</span>
  </div>
  <div class="abs portal-btn">PATIENT PORTAL</div>
</header>

<nav class="main-nav">
  <a class="active" style="left:99px;width:77px;text-align:center">Home</a>
  <a style="left:193px">About Us</a>
  <a style="left:315px">Services</a>
  <a style="left:427px">Conditions We Treat</a>
  <a style="left:643px">New Patients</a>
  <a style="left:796px">Contact Us</a>
  <svg class="nav-search" width="18" height="18" viewBox="0 0 18 18"><circle cx="7.5" cy="7.5" r="5" fill="none" stroke="#fff" stroke-width="2.2"/><path d="M11.3 11.3l4.5 4.5" stroke="#fff" stroke-width="2.4" stroke-linecap="round"/></svg>
</nav>

<section class="hero">
  <div class="hero-photo" role="img" aria-label="Black and white photo of a doctor with a stethoscope reviewing a clipboard with a patient"></div>
  <h1 class="hero-title">Maplecrest Behavioral Healthcare</h1>
  <p class="hero-sub">A step forward in your wellness journey</p>
  <div class="hero-btn">TAKE A SCREENING</div>
  <svg class="hero-arrow" style="left:38px" width="20" height="36" viewBox="0 0 20 36"><path d="M16 4L4 18l12 14" fill="none" stroke="rgba(255,255,255,.6)" stroke-width="2.5"/></svg>
  <svg class="hero-arrow" style="left:1140px" width="20" height="36" viewBox="0 0 20 36"><path d="M4 4l12 14L4 32" fill="none" stroke="rgba(255,255,255,.6)" stroke-width="2.5"/></svg>
  <svg class="hero-curve" width="1200" height="80" viewBox="0 0 1200 80" preserveAspectRatio="none"><path d="M0 80 L0 20 Q600 -30 1200 70 L1200 80 Z" fill="#fff"/></svg>
</section>

<section class="welcome">
  <h2 class="section-title">WELCOME TO MAPLECREST BEHAVIORAL HEALTHCARE</h2>
  <p>Nemo enim ipsam voluptatem quia voluptas sit aspernatur aut odit aut fugit, sed quia consequuntur magni dolores eos qui ratione voluptatem sequi nesciunt. Neque porro quisquam est, qui dolorem ipsum quia dolor sit amet, consectetur, adipisci velit, sed quia non numquam eius modi tempora incidunt ut labore et dolore magnam aliquam quaerat voluptatem.</p>
  <p>Ut enim ad minima veniam, quis nostrum exercitationem ullam corporis suscipit laboriosam, nisi ut aliquid ex ea commodi consequatur? Quis autem vel eum iure reprehenderit qui in ea voluptate velit esse quam nihil molestiae consequatur, vel illum qui dolorem eum fugiat.</p>
  <div class="outline-btn" style="left:458px;top:265px;width:282px;height:49px">READ MORE INFORMATION</div>
</section>

<section class="services">
  <h2 class="section-title">OUR SERVICES</h2>
  <article class="service-card" style="left:99px">
    <div class="service-photo" role="img" aria-label="Photo of a clinician taking a patient's blood pressure" style="background:linear-gradient(135deg,#f4ebe6,#d9cfca)"></div>
    <h3>Diagnostic Evaluation and Treatment</h3>
    <p>Sed do eiusmod tempor incididunt ut labore et dolore magna aliqua quis nostrud exercitation ullamco laboris nisi ut aliquip.</p>
  </article>
  <article class="service-card" style="left:355px">
    <div class="service-photo" role="img" aria-label="Photo of a doctor visiting a patient resting in bed" style="background:linear-gradient(135deg,#eef0f2,#c9cdd2)"></div>
    <h3>Substance Abuse Assessments</h3>
    <p>Sed do eiusmod tempor incididunt ut labore et dolore magna aliqua quis nostrud exercitation ullamco laboris nisi ut aliquip.</p>
  </article>
  <article class="service-card" style="left:611px">
    <div class="service-photo" role="img" aria-label="Photo of a counselor talking with a client in an office" style="background:linear-gradient(135deg,#e2e4e3,#9fa3a2)"></div>
    <h3>Bariatric Pre-surgical Consultation</h3>
    <p>Sed do eiusmod tempor incididunt ut labore et dolore magna aliqua quis nostrud exercitation ullamco laboris nisi ut aliquip.</p>
  </article>
  <article class="service-card" style="left:867px">
    <div class="service-photo" role="img" aria-label="Photo of a clinician with a young child and parent" style="background:linear-gradient(135deg,#f1e6dc,#c8b9a8)"></div>
    <h3>Early Childhood Assessments</h3>
    <p>Sed do eiusmod tempor incididunt ut labore et dolore magna aliqua quis nostrud exercitation ullamco laboris nisi ut aliquip.</p>
  </article>
  <div class="outline-btn" style="left:519px;top:537px;width:162px;height:38px;font-weight:400">VIEW MORE</div>
</section>

<section class="faq">
  <div class="faq-photo" role="img" aria-label="Blue tinted photo of scattered cards with a question mark"></div>
  <h2 class="section-title">FAQS</h2>
  <div class="faq-list">
    <p class="faq-q">Q. What do I need to bring with me to my first visit?</p>
    <p class="faq-a">A- Insurance card, patient forms found on our Form's page.</p>
    <p class="faq-q">Q- How long do I have to wait to be seen?</p>
    <p class="faq-a">A- We try to have very little wait time for your convenience</p>
    <p class="faq-q">Q- What typs of insurance do you accept?</p>
    <p class="faq-a">A- We accept a large variety of insurance plans</p>
  </div>
</section>

<section class="news">
  <h2 class="section-title">LATEST NEWS</h2>
  <p class="news-intro">At vero eos et accusamus et iusto odio dignissimos ducimus qui blanditiis praesentium voluptatum deleniti atque corrupti quos dolores et quas molestias</p>
  <article class="news-item" style="left:101px">
    <div class="news-photo" role="img" aria-label="Photo of a stressed woman holding her head" style="background:linear-gradient(135deg,#d8dde2,#a3acb5)"></div>
    <h3>Numquam Eius Modi Tempora</h3>
    <p>Class aptent taciti sociosqu ad litora torquent per co nubia nostra per inceptos hymenaeos</p>
    <p class="news-date">25 FEB 2017</p>
  </article>
  <article class="news-item" style="left:446px">
    <div class="news-photo" role="img" aria-label="Photo of three generations of women smiling together" style="background:linear-gradient(135deg,#e7d6c6,#b79c86)"></div>
    <h3>Occaecat Cupidatat&nbsp; Proident</h3>
    <p>Class aptent taciti sociosqu ad litora torquent per co nubia nostra per inceptos hymenaeos</p>
    <p class="news-date">25 FEB 2017</p>
  </article>
  <article class="news-item" style="left:791px">
    <div class="news-photo" role="img" aria-label="Photo of a smiling senior woman with a caregiver" style="background:linear-gradient(135deg,#e4eef4,#a9c4d6)"></div>
    <h3>Officia Deserunt Mollit Anim</h3>
    <p>Class aptent taciti sociosqu ad litora torquent per co nubia nostra per inceptos hymenaeos</p>
    <p class="news-date">25 FEB 2017</p>
  </article>
</section>

<section class="contact">
  <h2 class="section-title">CONTACT US</h2>
  <div class="contact-info">
    <div class="contact-row">
      <svg width="14" height="18" viewBox="0 0 14 18"><path d="M7 0a7 7 0 0 0-7 7c0 5 7 11 7 11s7-6 7-11a7 7 0 0 0-7-7zm0 9.5A2.5 2.5 0 1 1 7 4.5a2.5 2.5 0 0 1 0 5z" fill="#29b5e8"/></svg>
      <span><b>Address:</b> 214 Linden Way, Fayetteville,<br>GA 30214</span>
    </div>
    <div class="contact-row">
      <svg width="16" height="16" viewBox="0 0 24 24"><path d="M6.6 10.8a15.1 15.1 0 0 0 6.6 6.6l2.2-2.2a1 1 0 0 1 1-.25c1.1.37 2.3.57 3.6.57a1 1 0 0 1 1 1V20a1 1 0 0 1-1 1C10.6 21 3 13.4 3 4a1 1 0 0 1 1-1h3.5a1 1 0 0 1 1 1c0 1.3.2 2.5.57 3.6a1 1 0 0 1-.25 1z" fill="#29b5e8"/></svg>
      <span><b>Call Us:</b> (770) 555-0142</span>
    </div>
    <div class="contact-row">
      <svg width="18" height="14" viewBox="0 0 18 14"><rect x="1" y="1" width="16" height="12" fill="none" stroke="#29b5e8" stroke-width="1.8"/><path d="M1 1l8 6 8-6" fill="none" stroke="#29b5e8" stroke-width="1.8"/></svg>
      <span><b>Email:</b> hello@maplecrestbh.com</span>
    </div>
    <div class="social-dot"></div>
  </div>
  <form class="contact-form">
    <div class="field" style="left:0;top:0;width:262px">First Name *</div>
    <div class="field" style="left:290px;top:0;width:262px">Last Name *</div>
    <div class="field" style="left:0;top:60px;width:552px">Email *</div>
    <div class="field" style="left:0;top:120px;width:262px">Phone Number *</div>
    <div class="field" style="left:290px;top:120px;width:262px">Company Name</div>
    <div class="field" style="left:0;top:181px;width:552px;height:92px">How can we help *</div>
    <div class="submit-btn">SUBMIT NOW</div>
  </form>
</section>

<footer class="site-footer">© 2017 MBHC.&nbsp; All right reserved.&nbsp; Term of Use</footer>

</body>
</html>
```